2 x Digitize Logo | 2 x Business Cards | 2 x Fridge Magnets

We require 6 deliverables:
1. Residential logo redrawn (same just high quality for large print format).
2. Corporate logo redrawn (minor changes to wording and high quality for large print format).
3. New business card design for Furniture Removals (residential)
4. New business card design for Corporate Relocations (business)
5. New Fridge magnet for Furniture removals (residential)
6. New fridge magnet for Corporate Relocations (business)
1. Residential Logo
a. We require the logo to be translated into a high quality digital image with no modifications.
(see attached resilogo.jpg)
2. Residential Logo
a. We require the logo to be edited (add the word corporate relocations) be translated into a high quality digital image.
(see attached corplogo.jpg)
3. Using the resilogo please make a new business card for our business.
a. Please see the web site https://www.larkbendcarters.com.au for colours and inspiration.
b. The residential business card needs the following information:
i. Business Name (using the residential logo).
ii. Free Call: 1800 LB Cart (the L, B and Cart much be the same colour as the logo).
iii. Website: www.LarkbendCarters.com.au
iv. Address: 4/17 Ormsdale Court, VIC 3264
v. Email: cart@LarkbendCarters.com.au
vi. backof Card:
Review our service
www.PennantOrbit.com.au
Services: Local, Country, Interstate | Furniture Removals | Piano, Billiard Tables & Antiques
4. Using the corplogo please make a new business card for our business.
b. The corporate business card needs the following information:
i. Business Name (using the corporate logo).
v. Email: corporate@LarkbendCarters.com.au
vi. Back of Card:
Review our service
www.PennantOrbit.com.au
Services: Corporate relocations | Office equipment moves | Packing Service | Packing Materials
5. Using the resilogo please make a new fridge magent for our business.
b. The residential fidge magnet needs the following information:
iv. Services: Local, Country, Interstate | Furniture Removals | Piano, Billiard Tables & Antiques
6. Using the corplogo please make a new fridge magent for our business.
b. The corporate fidge magnet needs the following information:
iv. Services: Local, Country, Interstate | Corporate relocations
Target Market(s)
Residential Furniture Removals and Corporate Office relocations
Industry/Entity Type
Business
Contact Information for Business Card
Please see full brief for six items required
Requirements
Must have
- Clean simple, easy to read
Nice to have
- fresh, stand out, eye catching
Should not have
- plain, standard, boring, general

```html
<!DOCTYPE html>
<html lang="en">
<head>
<meta charset="utf-8">
<title>Larkbend Carters – Corporate Business Card</title>
<link rel="stylesheet" href="https://fonts.googleapis.com/css2?family=Source+Sans+3:wght@400;600&display=swap">
<style>
  :root {
    --green: #00743b;
    --red: #c1272d;
    --white: #ffffff;
    --ink: #1d1d1b;
    --backdrop: #ecebe8;
  }
  * { margin: 0; padding: 0; box-sizing: border-box; }
  html, body {
    width: 1109px; height: 1200px; overflow: hidden;
    background: var(--backdrop);
    font-family: "Source Sans 3", Arial, sans-serif;
    color: var(--ink);
  }
  .sheet { position: relative; width: 1109px; height: 1200px; }
  .card-slot {
    position: absolute; left: 124px; width: 860px; height: 531px;
    box-shadow: 0 6px 20px rgba(0,0,0,0.18);
  }
  .card-slot--front { top: 46px; }
  .card-slot--back { top: 622px; }
  .card {
    position: absolute; top: 0; left: 0;
    width: 654px; height: 404px;
    background: var(--white);
    transform: scale(1.315); transform-origin: 0 0;
    overflow: hidden;
  }
  .card__shape { position: absolute; inset: 0; width: 654px; height: 404px; }
  .brand {
    position: absolute; width: 300px; text-align: center;
  }
  .brand__name {
    display: flex; align-items: center; justify-content: center; gap: 8px;
    font-weight: 600; font-size: 25px; letter-spacing: 0.5px;
    color: var(--green); text-transform: uppercase;
  }
  .brand__dot { width: 14px; height: 14px; border-radius: 50%; background: var(--red); }
  .brand__tagline {
    margin-top: 4px; font-size: 20px; color: var(--green);
    text-transform: uppercase; letter-spacing: 0.3px;
  }
  .front .brand { left: 320px; top: 112px; }
  .back .brand { left: 9px; top: 112px; }

  .services { position: absolute; left: 34px; top: 233px; color: var(--white); }
  .services__title { font-size: 20px; letter-spacing: 0.3px; margin-bottom: 14px; }
  .services__list { list-style: none; font-size: 17px; line-height: 23.7px; }
  .services__list li::before { content: "●"; font-size: 11px; margin-right: 5px; vertical-align: 2px; }

  .contact { position: absolute; list-style: none; font-size: 17px; }
  .contact li { display: flex; align-items: center; gap: 5px; height: 23.5px; white-space: nowrap; }
  .contact li.contact__address { margin-top: 8px; }
  .contact svg { width: 12px; height: 12px; fill: var(--green); flex: none; }
  .contact .accent { color: var(--red); font-weight: 600; }
  .front .contact { right: 24px; top: 266px; }
  .front .contact li { justify-content: flex-end; }
  .back .contact { left: 28px; top: 266px; }

  .review {
    position: absolute; left: 370px; width: 250px; top: 319px;
    text-align: center;
  }
  .review__title { font-size: 16px; font-weight: 600; color: var(--red); text-transform: uppercase; }
  .review__url { font-size: 17px; color: var(--white); margin-top: 4px; }
</style>
</head>
<body>
<main class="sheet">

  <section class="card-slot card-slot--front">
    <article class="card front">
      <svg class="card__shape" viewBox="0 0 654 404" aria-hidden="true">
        <polygon points="0,0 265,0 192,62 335,404 0,404" fill="var(--green)"/>
        <polyline points="265,0 192,62 335,404" fill="none" stroke="var(--red)" stroke-width="3"/>
      </svg>

      <div class="services">
        <h2 class="services__title">SERVICES</h2>
        <ul class="services__list">
          <li>Corporate Relocations</li>
          <li>Office Equipment Moves</li>
          <li>Packing Service</li>
          <li>Packing Materials</li>
        </ul>
      </div>

      <div class="brand">
        <div class="brand__name"><span class="brand__dot"></span>Larkbend Carters</div>
        <div class="brand__tagline">Corporate Relocations</div>
      </div>

      <ul class="contact">
        <li>1800 <span class="accent">LB</span> <span class="accent">Cart</span> / 1800 52 27 84
          <svg viewBox="0 0 24 24"><path d="M6.6 10.8a15 15 0 0 0 6.6 6.6l2.2-2.2a1 1 0 0 1 1-.25 11.4 11.4 0 0 0 3.6.57 1 1 0 0 1 1 1V20a1 1 0 0 1-1 1A17 17 0 0 1 3 4a1 1 0 0 1 1-1h3.5a1 1 0 0 1 1 1c0 1.25.2 2.45.57 3.57a1 1 0 0 1-.25 1z"/></svg></li>
        <li>corporate@LarkbendCarters.com.au
          <svg viewBox="0 0 24 24"><path d="M2 5h20v14H2zm2 2v.5l8 5 8-5V7zm0 3v7h16v-7l-8 5z"/></svg></li>
        <li>www.LarkbendCarters.com.au
          <svg viewBox="0 0 24 24"><path d="M12 2a10 10 0 1 0 0 20 10 10 0 0 0 0-20zm-1 17.9A8 8 0 0 1 4.1 11H7v2l4 4zm6.9-2.9A2 2 0 0 0 16 16h-1v-3a1 1 0 0 0-1-1H8v-2h2a1 1 0 0 0 1-1V7h2a2 2 0 0 0 2-2v-.4A8 8 0 0 1 17.9 17z"/></svg></li>
        <li class="contact__address">4/17 Ormsdale Court, VIC 3264
          <svg viewBox="0 0 24 24"><path d="M12 2a7 7 0 0 0-7 7c0 5.2 7 13 7 13s7-7.8 7-13a7 7 0 0 0-7-7zm0 9.5A2.5 2.5 0 1 1 12 6.5a2.5 2.5 0 0 1 0 5z"/></svg></li>
      </ul>
    </article>
  </section>

  <section class="card-slot card-slot--back">
    <article class="card back">
      <svg class="card__shape" viewBox="0 0 654 404" aria-hidden="true">
        <polygon points="387,0 654,0 654,404 319,404 459,62" fill="var(--green)"/>
        <polyline points="387,0 459,62 319,404" fill="none" stroke="var(--red)" stroke-width="3"/>
      </svg>

      <div class="brand">
        <div class="brand__name"><span class="brand__dot"></span>Larkbend Carters</div>
        <div class="brand__tagline">Corporate Relocations</div>
      </div>

      <ul class="contact">
        <li><svg viewBox="0 0 24 24"><path d="M6.6 10.8a15 15 0 0 0 6.6 6.6l2.2-2.2a1 1 0 0 1 1-.25 11.4 11.4 0 0 0 3.6.57 1 1 0 0 1 1 1V20a1 1 0 0 1-1 1A17 17 0 0 1 3 4a1 1 0 0 1 1-1h3.5a1 1 0 0 1 1 1c0 1.25.2 2.45.57 3.57a1 1 0 0 1-.25 1z"/></svg>
          1800 <span class="accent">LB</span> <span class="accent">Cart</span> / 1800 52 27 84</li>
        <li><svg viewBox="0 0 24 24"><path d="M2 5h20v14H2zm2 2v.5l8 5 8-5V7zm0 3v7h16v-7l-8 5z"/></svg>
          corporate@LarkbendCarters.com.au</li>
        <li><svg viewBox="0 0 24 24"><path d="M12 2a10 10 0 1 0 0 20 10 10 0 0 0 0-20zm-1 17.9A8 8 0 0 1 4.1 11H7v2l4 4zm6.9-2.9A2 2 0 0 0 16 16h-1v-3a1 1 0 0 0-1-1H8v-2h2a1 1 0 0 0 1-1V7h2a2 2 0 0 0 2-2v-.4A8 8 0 0 1 17.9 17z"/></svg>
          www.LarkbendCarters.com.au</li>
        <li class="contact__address"><svg viewBox="0 0 24 24"><path d="M12 2a7 7 0 0 0-7 7c0 5.2 7 13 7 13s7-7.8 7-13a7 7 0 0 0-7-7zm0 9.5A2.5 2.5 0 1 1 12 6.5a2.5 2.5 0 0 1 0 5z"/></svg>
          4/17 Ormsdale Court, VIC 3264</li>
      </ul>

      <div class="review">
        <div class="review__title">Review our service</div>
        <div class="review__url">www.PennantOrbit.com.au</div>
      </div>
    </article>
  </section>

</main>
</body>
</html>
```